World Class Presentation folder for a National Designer of innovative building products

We are a National Designer, Manufacturer, and distributor of aluminum and stainless Balconies, Railings, Sunshades, and Patio Covers. We sell our products and services to the very best commercial condo and residential builders in the country. This Brochure folder will be the first piece of literature that we give to our customers, and want to WOW them at first glance with a world-class design and look.

We already have a logo and website but would like you to visit https://harborlineframeworks.example and view the projects and product information to help inspire you to create an award-winning piece of literature for us.

Besides putting literature in it, the folder must have a place to hold a business card.

Thank you in advance for your great designs, and I look forward to working with you.
Dean Holtzmarrick
President | Pacific, WA
417.629.5810 ext 305

```html
<!DOCTYPE html>
<html lang="en">
<head>
<meta charset="utf-8">
<title>Harborline Frameworks – Presentation Folder</title>
<link href="https://fonts.googleapis.com/css2?family=Montserrat:wght@500;600;700&family=Ubuntu:wght@400;500&display=swap" rel="stylesheet">
<style>
  :root {
    --canvas: #d9d9d9;
    --paper: #ffffff;
    --ink-dark: #1b1b1c;
    --ink-mid: #2a2a2b;
    --brand-red: #c8173f;
    --text-dark: #222222;
    --text-light: #ffffff;
    --rule: #cfcfcf;
  }
  * { margin: 0; padding: 0; box-sizing: border-box; }
  html, body { width: 1200px; height: 1044px; overflow: hidden; }
  body { background: var(--canvas); font-family: "Ubuntu", sans-serif; position: relative; }

  .folder { position: absolute; left: 124px; top: 32px; width: 951px; height: 979px; }
  .spread { position: absolute; left: 0; top: 0; width: 951px; height: 751px; background: var(--paper); overflow: hidden; box-shadow: 0 2px 6px rgba(0,0,0,.18); }
  .spread-art { position: absolute; left: 0; top: 0; width: 951px; height: 751px; }
  .spine { position: absolute; left: 475px; top: 0; width: 2px; height: 751px; background: linear-gradient(to right, rgba(0,0,0,.08), rgba(0,0,0,0)); }

  .brand-name { font-family: "Montserrat", sans-serif; font-weight: 700; text-transform: uppercase; display: flex; align-items: center; gap: 10px; }
  .brand-mark { width: 14px; height: 14px; background: var(--brand-red); flex: none; }

  .back-brand { position: absolute; left: 33px; top: 188px; color: var(--text-light); font-size: 22px; line-height: 1.05; letter-spacing: .5px; }
  .tagline { position: absolute; left: 33px; top: 272px; width: 290px; color: var(--text-light); font-family: "Montserrat", sans-serif; font-weight: 500; font-size: 11.5px; line-height: 13.5px; text-transform: uppercase; }
  .products-title { position: absolute; left: 33px; top: 320px; color: var(--brand-red); font-family: "Montserrat", sans-serif; font-weight: 500; font-size: 22px; }
  .product-list { position: absolute; left: 33px; top: 362px; list-style: none; }
  .product-list li { display: flex; align-items: center; gap: 5px; color: var(--text-light); font-size: 11.5px; height: 19px; }
  .product-list svg { width: 11px; height: 11px; flex: none; }
  .badges { position: absolute; left: 30px; top: 501px; display: flex; gap: 17px; }
  .badge { width: 31px; height: 31px; border-radius: 50%; border: 2px solid var(--brand-red); }

  .office { position: absolute; top: 651px; color: var(--text-dark); }
  .office-wa { left: 37px; }
  .office-or { left: 305px; }
  .office h3 { font-family: "Montserrat", sans-serif; font-weight: 600; font-size: 12px; color: var(--brand-red); margin-bottom: 6px; letter-spacing: .3px; }
  .office p { display: flex; align-items: flex-start; gap: 7px; font-size: 10px; line-height: 15px; }
  .office svg { width: 10px; height: 10px; flex: none; margin-top: 2px; }
  .office .indent { padding-left: 17px; }
  .office-divider { position: absolute; left: 240px; top: 649px; width: 1px; height: 79px; background: var(--rule); }

  .front-brand { position: absolute; left: 476px; top: 40px; width: 475px; justify-content: center; color: var(--ink-dark); font-size: 30px; letter-spacing: 1px; }

  .front-headline { position: absolute; left: 493px; top: 640px; color: var(--text-dark); font-family: "Montserrat", sans-serif; font-weight: 600; font-size: 14px; line-height: 19px; text-transform: uppercase; }
  .web-link { position: absolute; left: 484px; top: 718px; display: flex; align-items: center; gap: 8px; color: var(--text-light); font-size: 12px; }
  .web-link svg { width: 12px; height: 12px; }

  .pocket { position: absolute; left: 0; top: 0; width: 951px; height: 979px; pointer-events: none; }
</style>
</head>
<body>
<div class="folder">
  <section class="spread">
    <svg class="spread-art" viewBox="0 0 951 751" aria-hidden="false">
      <defs>
        <linearGradient id="bandDark" x1="0" y1="0" x2="1" y2="0">
          <stop offset="0" stop-color="#141414"/>
          <stop offset=".5" stop-color="#2b2b2c"/>
          <stop offset="1" stop-color="#1e1e1f"/>
        </linearGradient>
        <linearGradient id="terrace" x1="0" y1="0" x2="0" y2="1">
          <stop offset="0" stop-color="#8fb4d8"/>
          <stop offset=".35" stop-color="#b9c7b0"/>
          <stop offset=".55" stop-color="#6f7a3e"/>
          <stop offset=".75" stop-color="#4a403a"/>
          <stop offset="1" stop-color="#2f2926"/>
        </linearGradient>
        <linearGradient id="hexA" x1="0" y1="0" x2="0" y2="1"><stop offset="0" stop-color="#9fb9cf"/><stop offset="1" stop-color="#2d2f31"/></linearGradient>
        <linearGradient id="hexB" x1="0" y1="0" x2="0" y2="1"><stop offset="0" stop-color="#a9bfd6"/><stop offset=".55" stop-color="#9a6a52"/><stop offset="1" stop-color="#6c9a4a"/></linearGradient>
        <linearGradient id="hexC" x1="0" y1="0" x2="0" y2="1"><stop offset="0" stop-color="#e9ecef"/><stop offset=".6" stop-color="#6e6257"/><stop offset="1" stop-color="#5f8f3e"/></linearGradient>
      </defs>
      <rect x="0" y="119" width="951" height="506" fill="url(#bandDark)"/>
      <path d="M478 141 L951 141 L951 605 L173 605 C260 470 380 290 478 141 Z" fill="url(#terrace)" role="img" aria-label="Rooftop terrace with wicker lounge chairs, wood decking and aluminum railing in front of city towers"/>
      <path d="M464 141 L488 141 C390 290 272 470 186 605 L160 605 C248 470 368 290 464 141 Z" fill="var(--brand-red)"/>
      <g stroke="#ffffff" stroke-width="4">
        <polygon points="784,459 836,489 836,549 784,579 732,549 732,489" fill="url(#hexA)" role="img" aria-label="Glass balcony railing on a high-rise"/>
        <polygon points="726,565 778,595 778,655 726,685 674,655 674,595" fill="url(#hexB)" role="img" aria-label="Apartment building with balconies"/>
        <polygon points="864,576 916,606 916,666 864,696 812,666 812,606" fill="url(#hexC)" role="img" aria-label="White patio cover over a backyard deck"/>
      </g>
      <polygon points="478,713 706,713 714,737 478,737" fill="var(--brand-red)"/>
    </svg>
    <div class="spine"></div>

    <div class="brand-name back-brand"><span class="brand-mark"></span><span>Harborline<br>Frameworks</span></div>
    <p class="tagline">Premier manufacturer &amp; distributer of aluminum railing, balcony, and sunshade systems</p>
    <h2 class="products-title">OUR PRODUCTS</h2>
    <ul class="product-list">
      <li><svg viewBox="0 0 12 12"><circle cx="6" cy="6" r="5" fill="none" stroke="#c8173f" stroke-width="1.4"/><path d="M3.5 6.2 L5.3 7.8 L8.5 4.4" fill="none" stroke="#c8173f" stroke-width="1.4"/></svg>Railling System</li>
      <li><svg viewBox="0 0 12 12"><circle cx="6" cy="6" r="5" fill="none" stroke="#c8173f" stroke-width="1.4"/><path d="M3.5 6.2 L5.3 7.8 L8.5 4.4" fill="none" stroke="#c8173f" stroke-width="1.4"/></svg>Stainless Steel Cable</li>
      <li><svg viewBox="0 0 12 12"><circle cx="6" cy="6" r="5" fill="none" stroke="#c8173f" stroke-width="1.4"/><path d="M3.5 6.2 L5.3 7.8 L8.5 4.4" fill="none" stroke="#c8173f" stroke-width="1.4"/></svg>Balcony Systems</li>
      <li><svg viewBox="0 0 12 12"><circle cx="6" cy="6" r="5" fill="none" stroke="#c8173f" stroke-width="1.4"/><path d="M3.5 6.2 L5.3 7.8 L8.5 4.4" fill="none" stroke="#c8173f" stroke-width="1.4"/></svg>Sunshade Systems</li>
      <li><svg viewBox="0 0 12 12"><circle cx="6" cy="6" r="5" fill="none" stroke="#c8173f" stroke-width="1.4"/><path d="M3.5 6.2 L5.3 7.8 L8.5 4.4" fill="none" stroke="#c8173f" stroke-width="1.4"/></svg>Canopy Systems</li>
      <li><svg viewBox="0 0 12 12"><circle cx="6" cy="6" r="5" fill="none" stroke="#c8173f" stroke-width="1.4"/><path d="M3.5 6.2 L5.3 7.8 L8.5 4.4" fill="none" stroke="#c8173f" stroke-width="1.4"/></svg>Pation Cover Systems</li>
    </ul>
    <div class="badges"><span class="badge"></span><span class="badge"></span><span class="badge"></span></div>

    <div class="office office-wa">
      <h3>WASHINGTON</h3>
      <p><svg viewBox="0 0 10 10"><path d="M5 0.5 C2.8 0.5 1.6 2 1.6 3.8 C1.6 6 5 9.5 5 9.5 C5 9.5 8.4 6 8.4 3.8 C8.4 2 7.2 0.5 5 0.5 Z" fill="#c8173f"/><circle cx="5" cy="3.7" r="1.3" fill="#fff"/></svg>4102 Cedar Bend Rd SE</p>
      <p class="indent">Pacific, WA 98051</p>
      <p><svg viewBox="0 0 10 10"><path d="M2 0.8 L3.6 0.8 L4.3 3 L3.1 3.9 C3.7 5.2 4.8 6.3 6.1 6.9 L7 5.7 L9.2 6.4 L9.2 8 C9.2 8.7 8.6 9.2 7.9 9.2 C4 9 1 6 0.8 2.1 C0.8 1.4 1.3 0.8 2 0.8 Z" fill="#c8173f"/></svg>417-629-5810</p>
      <p><svg viewBox="0 0 10 10"><rect x="1" y="3" width="8" height="5.5" rx="1" fill="#c8173f"/><rect x="2.8" y="1" width="4.4" height="2.5" fill="#c8173f"/><rect x="2.8" y="5.5" width="4.4" height="1.4" fill="#fff"/></svg>877-512-6034</p>
    </div>
    <div class="office-divider"></div>
    <div class="office office-or">
      <h3>OREGON</h3>
      <p><svg viewBox="0 0 10 10"><path d="M5 0.5 C2.8 0.5 1.6 2 1.6 3.8 C1.6 6 5 9.5 5 9.5 C5 9.5 8.4 6 8.4 3.8 C8.4 2 7.2 0.5 5 0.5 Z" fill="#c8173f"/><circle cx="5" cy="3.7" r="1.3" fill="#fff"/></svg>9081 NE Alder Crest St.</p>
      <p class="indent">Portland, OR 97236</p>
      <p><svg viewBox="0 0 10 10"><path d="M2 0.8 L3.6 0.8 L4.3 3 L3.1 3.9 C3.7 5.2 4.8 6.3 6.1 6.9 L7 5.7 L9.2 6.4 L9.2 8 C9.2 8.7 8.6 9.2 7.9 9.2 C4 9 1 6 0.8 2.1 C0.8 1.4 1.3 0.8 2 0.8 Z" fill="#c8173f"/></svg>971-318-2207</p>
      <p><svg viewBox="0 0 10 10"><rect x="1" y="3" width="8" height="5.5" rx="1" fill="#c8173f"/><rect x="2.8" y="1" width="4.4" height="2.5" fill="#c8173f"/><rect x="2.8" y="5.5" width="4.4" height="1.4" fill="#fff"/></svg>971-318-2219</p>
    </div>

    <div class="brand-name front-brand"><span class="brand-mark"></span><span>Harborline Frameworks</span></div>
    <p class="front-headline">Stunning results<br>applications to<br>inspire</p>
    <div class="web-link"><svg viewBox="0 0 12 12" fill="none" stroke="#fff" stroke-width="1"><circle cx="6" cy="6" r="5"/><ellipse cx="6" cy="6" rx="2.2" ry="5"/><path d="M1 6 H11 M2 3.5 H10 M2 8.5 H10"/></svg>harborlineframeworks.example</div>
  </section>

  <svg class="pocket" viewBox="0 0 951 979">
    <defs>
      <linearGradient id="pocketShade" x1="0" y1="0" x2="1" y2="0">
        <stop offset="0" stop-color="#1d1d1e"/>
        <stop offset=".55" stop-color="#2c2c2d"/>
        <stop offset="1" stop-color="#0c0c0c"/>
      </linearGradient>
    </defs>
    <polygon points="478,757 951,757 951,979 503,979" fill="url(#pocketShade)"/>
    <line x1="616" y1="830" x2="646" y2="801" stroke="#8a8a8a" stroke-width="1"/>
    <line x1="807" y1="931" x2="836" y2="904" stroke="#8a8a8a" stroke-width="1"/>
  </svg>
</div>
</body>
</html>
```